SaaS Early tech startup business card design

Unique design for experience ecommerce platform company. the business cards will be used by executive members. conformance with color code is required.

```html
<!DOCTYPE html>
<html lang="en">
<head>
<meta charset="utf-8">
<title>Velto business card</title>
<link rel="stylesheet" href="https://fonts.googleapis.com/css2?family=Roboto:wght@400;700&display=swap">
<style>
  :root {
    --backdrop: #1c1c1c;
    --card: #2b2929;
    --card-front: #2a2828;
    --wordmark-front: #111111;
    --brand-blue: #0d77ad;
    --brand-teal: #19b5a2;
    --text-light: #d9d9d9;
    --tab-white: #f4f4f4;
    --tab-text: #2a2a2a;
  }
  * { margin: 0; padding: 0; box-sizing: border-box; }
  html, body { width: 1200px; height: 874px; overflow: hidden; background: var(--backdrop); }
  body { font-family: 'Roboto', sans-serif; position: relative; }

  .card {
    position: absolute;
    left: 320px;
    width: 560px;
    height: 320px;
    overflow: hidden;
    border-radius: 2px;
  }
  .card--front { top: 90px; background: var(--card-front); }
  .card--back { top: 464px; background: var(--card); }

  .front-wordmark {
    position: absolute;
    inset: 0;
    display: flex;
    align-items: center;
    justify-content: center;
    font-weight: 700;
    font-size: 124px;
    letter-spacing: -2px;
    color: var(--wordmark-front);
  }

  .back-wordmark {
    position: absolute;
    left: 52px;
    top: 92px;
    font-weight: 700;
    font-size: 78px;
    letter-spacing: -1px;
    color: var(--brand-teal);
    line-height: 1;
  }

  .divider {
    position: absolute;
    left: 300px;
    top: 66px;
    width: 1px;
    height: 150px;
    background: var(--brand-blue);
  }

  .contact { position: absolute; left: 322px; top: 66px; color: var(--text-light); }
  .contact__name { font-weight: 700; font-size: 21px; color: var(--brand-blue); line-height: 1.1; }
  .contact__title { font-weight: 700; font-size: 13px; color: var(--brand-teal); margin-bottom: 10px; }
  .contact__address { font-size: 12.5px; line-height: 1.35; margin-bottom: 8px; }
  .contact__list { list-style: none; font-size: 12.5px; line-height: 1.45; }
  .contact__list li { display: flex; align-items: center; gap: 7px; }
  .contact__list svg { width: 11px; height: 11px; flex: none; }

  .pixel-band {
    position: absolute;
    left: 0;
    bottom: 44px;
    width: 340px;
    height: 13px;
    background: linear-gradient(90deg, #19b5a2, #0f8fb4, #1ab8a6, #0d77ad, #19b5a2, #0d77ad);
  }

  .web-tab {
    position: absolute;
    right: 0;
    bottom: 0;
    width: 220px;
    height: 57px;
    background: var(--tab-white);
    border-top-left-radius: 40px;
    display: flex;
    align-items: center;
    justify-content: center;
    font-size: 15px;
    letter-spacing: 2px;
    color: var(--tab-text);
  }
  .web-tab strong { font-weight: 700; }
</style>
</head>
<body>
  <section class="card card--front" aria-label="Card front">
    <div class="front-wordmark">velto</div>
  </section>

  <section class="card card--back" aria-label="Card back">
    <div class="back-wordmark">velto</div>
    <div class="divider"></div>

    <div class="contact">
      <div class="contact__name">Daniel Reyes</div>
      <div class="contact__title">President</div>
      <div class="contact__address">1420 Harbor View Road<br>Juneau, Alaska 99801</div>
      <ul class="contact__list">
        <li>
          <svg viewBox="0 0 12 12" aria-hidden="true"><path fill="#19b5a2" d="M2.5 1l2 2.2-1 1.3c.7 1.5 1.7 2.5 3.2 3.2l1.3-1 2.2 2-1.2 1.8C5 10.2 1.8 7 .8 2.2z"/></svg>
          555-214-7730
        </li>
        <li>
          <svg viewBox="0 0 12 12" aria-hidden="true"><rect x="3" y="0.8" width="6" height="10.4" rx="1" fill="none" stroke="#19b5a2" stroke-width="1.3"/></svg>
          555-618-2049
        </li>
        <li>
          <svg viewBox="0 0 12 12" aria-hidden="true"><rect x="3" y="1" width="6" height="3" fill="#19b5a2"/><rect x="1" y="4.5" width="10" height="5" rx="1" fill="#19b5a2"/><rect x="3" y="8" width="6" height="3" fill="#2b2929" stroke="#19b5a2"/></svg>
          555-307-4481
        </li>
        <li>
          <svg viewBox="0 0 12 12" aria-hidden="true"><rect x="1" y="2.5" width="10" height="7" fill="#19b5a2"/><path d="M1.5 3l4.5 3.5L10.5 3" fill="none" stroke="#2b2929" stroke-width="1"/></svg>
          name@velto.com
        </li>
      </ul>
    </div>

    <div class="pixel-band" role="img" aria-label="Band of teal and blue mosaic squares"></div>
    <div class="web-tab">www.<strong>velto</strong>.com</div>
  </section>
</body>
</html>
```